swimming pool Leak Detection Brochure

I would Like to create a pool leak detection brochure

Target Market(s)

High end Clients with inground swimming pools

Industry/Entity Type

Pool Service

Font styles to use
Other font styles liked:
• Im open to suggestions but using my website for ideas is suggested

Colors

Designer to choose colors to be used in the design.

Requirements
Must have
• Do you Have a Leak??
• Figuring out when your pool has a leak can be tough. Environmental factors do play a role in the water level, and just because your pool’s water is lower than normal does not mean it has a leak. Wind, humidity, and sun exposure all impact your rate of evaporation.
• Warning Signs of a Leak in Your Pool
• Your pool, fountain, or spa loses more than 1/4 an inch of water a day
• There are cracks in or around the pool decking
• You need to add water more than once a week
• Grass around the area is soggy
• Your pool deck is sinking or lifting
Nice to have
• PREPARING FOR A LEAK TEST
• To ensure you receive an accurate leak detection test, it is required that you have the pool vacuumed and cleaned beforehand. Dirt and debris in the pool can make it difficult to spot even large leaks. Likewise, the water should be as clear as possible. If your water is green it means mildew, algae, or fungi has infested it. Not only does this make it impossible to test for leaks, but it’s dangerous for our health. Finally our pool should be full to the normal level - we can’t find a leak that is not leaking! After your test, you will be confident knowing you have a pool/fountain/spa that is free of leaks or the Leak has been found and can be repaired Properly.

```html
<!DOCTYPE html>
<html lang="en">
<head>
<meta charset="utf-8">
<title>Bluecrest Pool Service – Leak Detection Brochure</title>
<link href="https://fonts.googleapis.com/css2?family=Roboto+Condensed:ital,wght@0,400;0,700;1,700;1,800&family=Open+Sans:ital,wght@0,400;0,600;0,700;1,400&display=swap" rel="stylesheet">
<style>
:root{
  --blue:#1560a8;
  --blue-dark:#0c3f78;
  --blue-light:#2b8fd6;
  --orange:#f07a1a;
  --ink:#333a44;
  --paper:#ffffff;
  --stage:#e4e7eb;
  --water:#3ba7e0;
  --water-deep:#1b6fb3;
}
*{margin:0;padding:0;box-sizing:border-box}
html,body{width:880px;height:1200px;overflow:hidden;background:var(--stage)}
body{font-family:"Open Sans",Arial,sans-serif;color:var(--ink);position:relative}
.spread{position:absolute;left:10px;width:860px;height:570px;display:flex;box-shadow:0 4px 14px rgba(0,0,0,.25)}
.spread--outside{top:20px}
.spread--inside{top:610px}
.panel{position:relative;width:430px;height:570px;background:var(--paper);overflow:hidden}
.abs{position:absolute}
svg.abs{display:block}

/* back panel */
.quote-mark{left:34px;top:40px;font:700 60px/1 "Roboto Condensed",sans-serif;color:#fff}
.testimonial{left:80px;top:58px;width:210px;font-size:10px;line-height:1.55;color:#fff;font-style:italic}
.testimonial-name{left:300px;top:200px;font:700 italic 13px "Roboto Condensed",sans-serif;color:#fff}
.avatar{left:290px;top:80px;width:100px;height:100px;border-radius:50%;border:4px solid #fff;background:radial-gradient(circle at 40% 35%,#c9d8e6,#6e8aa6)}
.contact{left:0;top:280px;width:430px;text-align:center;color:#fff}
.contact h3{font:700 18px "Roboto Condensed",sans-serif;letter-spacing:1px;margin-bottom:8px}
.contact p{font-size:10.5px;line-height:1.6}
.phone-bar{left:95px;top:385px;width:240px;height:40px;background:#fff;border-radius:20px;display:flex;align-items:center;justify-content:center;gap:10px;font:700 22px "Roboto Condensed",sans-serif;color:var(--blue)}

/* cover */
.pool-photo{left:0;top:0;width:430px;height:340px}
.brand-mark{left:155px;top:255px;width:120px;height:120px;border-radius:50%;background:#fff;border:5px solid var(--blue);display:flex;flex-direction:column;align-items:center;justify-content:center;text-align:center}
.brand-mark span{font:700 15px/1.15 "Roboto Condensed",sans-serif;color:var(--blue)}
.cover-title{left:40px;top:395px;width:260px;font:700 24px/1.2 "Roboto Condensed",sans-serif;color:var(--blue-dark)}
.cover-web{left:270px;top:455px;font:600 11px "Open Sans",sans-serif;color:var(--blue-dark)}

/* inside */
.heading{font:800 italic 22px/1.1 "Roboto Condensed",sans-serif;color:var(--orange);text-transform:uppercase;letter-spacing:.5px}
.subheading{font:700 12px "Roboto Condensed",sans-serif;color:var(--blue);text-transform:uppercase}
.body-copy{font-size:8.6px;line-height:1.5;color:var(--ink)}
.leak-list{left:28px;top:56px;width:380px;list-style:none}
.leak-list li{display:flex;gap:8px;align-items:flex-start;font-size:9px;line-height:1.45;margin-bottom:4px}
.leak-list li svg{flex:0 0 12px;margin-top:1px}
.leak-list .lead{font-weight:600}
.badges{left:28px;top:372px;width:380px;display:flex;gap:8px;flex-wrap:wrap}
.badge{width:58px;height:18px;border-radius:3px;background:var(--blue-dark)}
.badge--alt{background:#8a9099}
.equip-photo{left:28px;top:420px;width:180px;height:70px;background:linear-gradient(135deg,#4a5866,#9aa7b4);border-radius:4px}
.phone-band-text{left:80px;top:518px;font:700 24px "Roboto Condensed",sans-serif;color:#fff}
.benefit-lines{font:700 9.5px/1.5 "Open Sans",sans-serif;color:var(--orange)}
.service-photo{left:0;top:400px;width:200px;height:120px}
.web-band-text{left:220px;top:532px;font:600 12px "Open Sans",sans-serif;color:#fff}
</style>
</head>
<body>

<!-- OUTSIDE SPREAD -->
<section class="spread spread--outside">
  <article class="panel panel--back">
    <svg class="abs" width="430" height="570" viewBox="0 0 430 570" aria-hidden="true">
      <polygon points="0,20 430,0 430,470 0,470" fill="var(--blue)"/>
      <polygon points="0,20 430,0 430,12 0,40" fill="var(--blue-light)"/>
      <path d="M0 470 Q215 520 430 450 L430 570 L0 570 Z" fill="var(--blue-dark)"/>
      <path d="M0 505 Q215 560 430 490 L430 570 L0 570 Z" fill="var(--orange)"/>
      <path d="M0 530 Q215 580 430 520 L430 570 L0 570 Z" fill="var(--blue)"/>
    </svg>
    <div class="abs quote-mark">“</div>
    <p class="abs testimonial">Bluecrest found the leak in our pool within an afternoon and repaired it the same week. The team was courteous, clear about every step and left the deck spotless. We now trust them with all our weekly service.</p>
    <div class="abs avatar" role="img" aria-label="Portrait photo of a satisfied customer"></div>
    <div class="abs testimonial-name">Harold M.</div>
    <div class="abs contact">
      <h3>CONTACT US</h3>
      <p>Bluecrest Pool Service<br>78 Harbor Road, Unit 4<br>Warwick, RI 02886<br>Licensed &amp; Insured Pool Professionals</p>
    </div>
    <div class="abs phone-bar">
      <svg width="18" height="18" viewBox="0 0 24 24" aria-hidden="true"><path fill="var(--blue)" d="M6.6 10.8a15 15 0 0 0 6.6 6.6l2.2-2.2c.3-.3.7-.4 1-.2 1.1.4 2.3.6 3.6.6.6 0 1 .4 1 1V20c0 .6-.4 1-1 1A17 17 0 0 1 3 4c0-.6.4-1 1-1h3.5c.6 0 1 .4 1 1 0 1.3.2 2.5.6 3.6.1.3 0 .7-.2 1z"/></svg>
      401-555-0148
    </div>
  </article>

  <article class="panel panel--cover">
    <svg class="abs pool-photo" width="430" height="340" viewBox="0 0 430 340" role="img" aria-label="Photo of a luxury inground swimming pool with clear blue water">
      <defs><linearGradient id="poolGrad" x1="0" y1="0" x2="0" y2="1"><stop offset="0" stop-color="#7fb8d8"/><stop offset=".45" stop-color="var(--water)"/><stop offset="1" stop-color="var(--water-deep)"/></linearGradient></defs>
      <path d="M0 0 H430 V250 Q215 360 0 250 Z" fill="url(#poolGrad)"/>
      <path d="M0 250 Q215 360 430 250 L430 262 Q215 372 0 262 Z" fill="var(--blue)"/>
    </svg>
    <div class="abs brand-mark"><span>BLUECREST<br>POOL<br>SERVICE</span></div>
    <h1 class="abs cover-title">Dive Into Professional Pool Service &amp; Repair</h1>
    <div class="abs cover-web">www.bluecrestpools.example</div>
    <svg class="abs" style="left:0;top:470px" width="430" height="100" viewBox="0 0 430 100" aria-hidden="true">
      <path d="M0 20 Q215 70 430 0 L430 100 L0 100 Z" fill="var(--blue-dark)"/>
      <path d="M0 45 Q215 95 430 30 L430 100 L0 100 Z" fill="var(--orange)"/>
      <path d="M0 65 Q215 110 430 60 L430 100 L0 100 Z" fill="var(--blue)"/>
    </svg>
  </article>
</section>

<!-- INSIDE SPREAD -->
<section class="spread spread--inside">
  <article class="panel panel--leak">
    <h2 class="abs heading" style="left:28px;top:20px">Do you have a leak??</h2>
    <ul class="abs leak-list">
      <li><svg width="12" height="12" viewBox="0 0 12 12" aria-hidden="true"><circle cx="6" cy="6" r="6" fill="var(--blue)"/></svg><span>Figuring out when your pool has a leak can be tough. Environmental factors do play a role in the water level, and just because your pool’s water is lower than normal does not mean it has a leak. Wind, humidity, and sun exposure all impact your rate of evaporation.</span></li>
      <li><svg width="12" height="12" viewBox="0 0 12 12" aria-hidden="true"><circle cx="6" cy="6" r="6" fill="var(--blue)"/></svg><span class="lead">Warning Signs of a Leak in Your Pool</span></li>
      <li><svg width="12" height="12" viewBox="0 0 12 12" aria-hidden="true"><circle cx="6" cy="6" r="6" fill="var(--blue)"/></svg><span>Your pool, fountain, or spa loses more than 1/4 an inch of water a day</span></li>
      <li><svg width="12" height="12" viewBox="0 0 12 12" aria-hidden="true"><circle cx="6" cy="6" r="6" fill="var(--blue)"/></svg><span>There are cracks in or around the pool decking</span></li>
      <li><svg width="12" height="12" viewBox="0 0 12 12" aria-hidden="true"><circle cx="6" cy="6" r="6" fill="var(--blue)"/></svg><span>You need to add water more than once a week</span></li>
      <li><svg width="12" height="12" viewBox="0 0 12 12" aria-hidden="true"><circle cx="6" cy="6" r="6" fill="var(--blue)"/></svg><span>Grass around the area is soggy</span></li>
      <li><svg width="12" height="12" viewBox="0 0 12 12" aria-hidden="true"><circle cx="6" cy="6" r="6" fill="var(--blue)"/></svg><span>Your pool deck is sinking or lifting</span></li>
    </ul>
    <h2 class="abs heading" style="left:28px;top:228px">Preparing for a leak test?</h2>
    <p class="abs body-copy" style="left:28px;top:256px;width:380px">To ensure you receive an accurate leak detection test, it is required that you have the pool vacuumed and cleaned beforehand. Dirt and debris in the pool can make it difficult to spot even large leaks. Likewise, the water should be as clear as possible. If your water is green it means mildew, algae, or fungi has infested it. Not only does this make it impossible to test for leaks, but it’s dangerous for our health. Finally our pool should be full to the normal level – we can’t find a leak that is not leaking! After your test, you will be confident knowing you have a pool/fountain/spa that is free of leaks or the leak has been found and can be repaired properly.</p>
    <div class="abs badges">
      <span class="badge"></span><span class="badge badge--alt"></span><span class="badge"></span><span class="badge badge--alt"></span><span class="badge"></span><span class="badge badge--alt"></span>
    </div>
    <div class="abs equip-photo" role="img" aria-label="Photo of pool pumps, filters and leak detection equipment"></div>
    <svg class="abs" style="left:0;top:470px" width="430" height="100" viewBox="0 0 430 100" aria-hidden="true">
      <path d="M0 20 Q215 0 430 30 L430 100 L0 100 Z" fill="var(--blue-dark)"/>
      <path d="M0 30 Q215 10 430 40 L430 100 L0 100 Z" fill="var(--orange)"/>
      <circle cx="55" cy="62" r="16" fill="#fff"/>
      <path transform="translate(45 52) scale(.85)" fill="var(--orange)" d="M6.6 10.8a15 15 0 0 0 6.6 6.6l2.2-2.2c.3-.3.7-.4 1-.2 1.1.4 2.3.6 3.6.6.6 0 1 .4 1 1V20c0 .6-.4 1-1 1A17 17 0 0 1 3 4c0-.6.4-1 1-1h3.5c.6 0 1 .4 1 1 0 1.3.2 2.5.6 3.6.1.3 0 .7-.2 1z"/>
    </svg>
    <div class="abs phone-band-text">401-555-0148</div>
  </article>

  <article class="panel panel--services">
    <h2 class="abs heading" style="left:28px;top:18px;width:380px">Pool maintenance, cleaning, &amp; repairs in RI</h2>
    <div class="abs subheading" style="left:28px;top:72px">Bluecrest Pool Service, RI, CT</div>
    <p class="abs body-copy" style="left:28px;top:92px;width:380px">Serving Massachusetts, Rhode Island, and Connecticut, Bluecrest Pool Service stands ready to provide exceptional pool maintenance for the most valuable pool at your home or business. Whether it is a high-end vinyl liner, gunite, or fiberglass pool, our trained technicians deliver careful weekly cleaning, repair and seasonal care you can rely on.</p>
    <div class="abs subheading" style="left:28px;top:170px;font-size:13px;text-transform:none">Benefits of Bluecrest Pool Service</div>
    <p class="abs body-copy" style="left:28px;top:190px;width:380px">As a family owned and operated business, Bluecrest Pool Service treats every customer like a neighbor. We arrive on time, explain our findings in plain words and use quality parts on every job. From opening to closing, we keep your water clear, balanced and ready for swimming all season long.</p>
    <p class="abs body-copy" style="left:28px;top:262px;width:380px">Our certified team also provides a full range of services for every level of pool ownership, so you never need to search for another contractor again.</p>
    <p class="abs benefit-lines" style="left:28px;top:300px;width:380px">Your satisfaction is our number one priority!<br>For Pool Repair, Maintenance and Cleaning<br>Call Bluecrest Pool Service TODAY!</p>
    <svg class="abs service-photo" width="200" height="120" viewBox="0 0 200 120" role="img" aria-label="Photo of a technician servicing a backyard pool">
      <defs><linearGradient id="svcGrad" x1="0" y1="0" x2="1" y2="1"><stop offset="0" stop-color="#9ccbe6"/><stop offset="1" stop-color="var(--water-deep)"/></linearGradient></defs>
      <path d="M0 0 H200 Q170 80 200 120 H0 Z" fill="url(#svcGrad)"/>
    </svg>
    <svg class="abs" style="left:0;top:470px" width="430" height="100" viewBox="0 0 430 100" aria-hidden="true">
      <path d="M0 40 Q215 10 430 20 L430 100 L0 100 Z" fill="var(--orange)"/>
      <path d="M0 50 Q215 22 430 32 L430 100 L0 100 Z" fill="var(--blue)"/>
      <circle cx="205" cy="68" r="9" fill="#fff"/>
      <circle cx="205" cy="68" r="5" fill="none" stroke="var(--blue)" stroke-width="1.5"/>
    </svg>
    <div class="abs web-band-text">www.bluecrestpools.example</div>
  </article>
</section>

</body>
</html>
```